Corvane Capital Business Cards

These are professional business cards that are for my family office.
Put fake emails and phone numbers as of now until I finalize those components. This family office controls my families investments, assets, and future. The cards should be professional.
..
.
.
.
I just uploaded another variation of a logo I would like to see as a business card to I am inbeteen which logo to use

Target Market(s)

business

Industry/Entity Type

business

Contact Information for Business Card

Professional, wealth related, finance related.

Requirements
Must have
• Logo

```html
<!DOCTYPE html>
<html lang="en">
<head>
<meta charset="utf-8">
<title>Corvane Capital Business Cards</title>
<link rel="stylesheet" href="https://fonts.googleapis.com/css2?family=Cormorant+SC:wght@600&family=Tinos:wght@400;700&display=swap">
<style>
  :root {
    --page-bg: #d9dadc;
    --card-white: #ffffff;
    --card-shade: #ececec;
    --ink-navy: #1b1f30;
    --ink-grey: #55575c;
    --faint-ring: #e2e3e5;
  }
  * { box-sizing: border-box; margin: 0; padding: 0; }
  html, body {
    width: 1200px;
    height: 900px;
    overflow: hidden;
    background: var(--page-bg);
  }
  .canvas {
    position: relative;
    width: 1200px;
    height: 900px;
  }
  .card {
    position: absolute;
    width: 620px;
    height: 354px;
    overflow: hidden;
    background: linear-gradient(120deg, var(--card-white) 0%, var(--card-white) 45%, var(--card-shade) 100%);
    box-shadow: 0 10px 28px rgba(0, 0, 0, 0.22);
  }
  .card--front { left: 140px; top: 60px; }
  .card--back { left: 440px; top: 486px; }

  .faint-ring {
    position: absolute;
    width: 300px;
    height: 300px;
    border: 4px solid var(--faint-ring);
    border-radius: 50%;
  }
  .card--front .faint-ring { right: -90px; top: 40px; }
  .card--back .faint-ring { right: -110px; top: 120px; }

  .wordmark {
    font-family: "Cormorant SC", "Times New Roman", serif;
    font-weight: 600;
    color: var(--ink-navy);
    letter-spacing: 0.02em;
    white-space: nowrap;
  }
  .card--front .wordmark {
    position: absolute;
    left: 48px;
    top: 128px;
    font-size: 50px;
  }

  .brand-block {
    position: absolute;
    right: 42px;
    top: 30px;
    display: flex;
    flex-direction: column;
    align-items: center;
    gap: 10px;
  }
  .brand-block .brand-circle {
    width: 64px;
    height: 64px;
    border: 3px solid var(--ink-navy);
    border-radius: 50%;
  }
  .brand-block .wordmark { font-size: 24px; }

  .contact {
    position: absolute;
    left: 48px;
    bottom: 34px;
    font-family: "Tinos", "Times New Roman", serif;
    color: var(--ink-grey);
  }
  .contact__name {
    font-weight: 700;
    font-size: 19px;
    color: var(--ink-navy);
    letter-spacing: 0.02em;
  }
  .contact__role {
    font-size: 15px;
    margin-bottom: 18px;
  }
  .contact__list { list-style: none; }
  .contact__item {
    display: flex;
    align-items: center;
    gap: 10px;
    font-size: 15px;
    line-height: 1.6;
  }
  .contact__icon {
    width: 14px;
    height: 14px;
    flex: none;
    fill: none;
    stroke: var(--ink-navy);
    stroke-width: 2;
  }
  .contact__icon--solid { fill: var(--ink-navy); stroke: none; }
</style>
</head>
<body>
<main class="canvas">

  <section class="card card--front" aria-label="Card front">
    <div class="faint-ring" aria-hidden="true"></div>
    <h1 class="wordmark">Corvane Capital</h1>
  </section>

  <section class="card card--back" aria-label="Card back">
    <div class="faint-ring" aria-hidden="true"></div>
    <div class="brand-block">
      <div class="brand-circle" aria-hidden="true"></div>
      <div class="wordmark">Corvane Capital</div>
    </div>

    <div class="contact">
      <p class="contact__name">ELLIOT MARSH</p>
      <p class="contact__role">Director</p>
      <ul class="contact__list">
        <li class="contact__item">
          <svg class="contact__icon contact__icon--solid" viewBox="0 0 24 24" aria-hidden="true"><path d="M6.6 10.8a15.1 15.1 0 0 0 6.6 6.6l2.2-2.2a1 1 0 0 1 1-.25 11.4 11.4 0 0 0 3.6.57 1 1 0 0 1 1 1V20a1 1 0 0 1-1 1A17 17 0 0 1 3 4a1 1 0 0 1 1-1h3.5a1 1 0 0 1 1 1c0 1.25.2 2.45.57 3.57a1 1 0 0 1-.25 1z"/></svg>
          300-555-0142
        </li>
        <li class="contact__item">
          <svg class="contact__icon contact__icon--solid" viewBox="0 0 24 24" aria-hidden="true"><path d="M2 5h20v14H2z M2 5l10 8 10-8" /></svg>
          info@corvanecapital.com
        </li>
        <li class="contact__item">
          <svg class="contact__icon" viewBox="0 0 24 24" aria-hidden="true"><circle cx="12" cy="12" r="9"/><ellipse cx="12" cy="12" rx="4" ry="9"/><path d="M3 12h18M5 7h14M5 17h14"/></svg>
          www.corvanecapital.com
        </li>
        <li class="contact__item">
          <svg class="contact__icon" viewBox="0 0 24 24" aria-hidden="true"><path d="M12 22s7-7.5 7-13a7 7 0 0 0-14 0c0 5.5 7 13 7 13z"/><circle cx="12" cy="9" r="2.5"/></svg>
          00 dummy city, dummy place 0000
        </li>
      </ul>
    </div>
  </section>

</main>
</body>
</html>
```